Cat-products company needs smart, yet endearing, business card

We need a business card design for a new, but up-and-running, business based in Honolulu, Hawaii. The business is Purrnest Nook Co. Our first product is the most environmentally-friendly cat grass kit ever seen on the planet. Future products, currently in the R&D phase, will include a variety of exciting cat scratchers. We also do consulting work to help apartment-dwellers make their home more cat-friendly and, in the future, plan on doing full, custom installs of structure to create high walkways for cats.

Target Market(s)

Middle-aged, apartment-dwelling, middle-class workers who own 1 or more cats and who dote on them.

Industry/Entity Type

Pet Care

Contact Information for Business Card

A striking, professional, yet warm and friendly design is what we're after.

Font styles to use
Serif
Sans Serif
Other font styles liked:
• Comfortaa

Colors

Designer to choose colors to be used in the design.

Requirements
Must have
• The company logo: (see attachment)
• The company name: Purrnest Nook Co
• The web address: www.purrnestnookco.com
• Email: support@purrnestnookco.com
• Phone: +1 (808) 571 6023
• Update (Fri Jun 30 3017 7:45pm Hawaii Time) I would like, is possible, uploaded picture of the cat grass kit on the back of the card with some text along the lines of: Purrnest Nook Co - Maker Of The Leafiest Feline Sprout Set Yet
Nice to have
• A cat picture, cartoon, real or silhouette that illustrates cats in action and/or relaxing; ie using the apartment space to live, play and relax in and being well-contented.
• Most of the website is done in the font: Comfortaa. It might be nice to continue using this for brand consistency.
Should not have
• Hard-to-read fonts.

```html
<!DOCTYPE html>
<html lang="en">
<head>
<meta charset="UTF-8">
<title>Purrnest Nook Co — Business Card</title>
<link rel="stylesheet" href="https://fonts.googleapis.com/css2?family=Comfortaa:wght@400;700&display=swap">
<style>
  :root {
    --stage: #d6d6d6;
    --sky: #b9d1d6;
    --sand: #e9dcbb;
    --cocoa: #56342f;
    --marigold: #f6b000;
    --slate-teal: #5f8a9b;
    --ink: #3b2622;
  }
  * { box-sizing: border-box; margin: 0; padding: 0; }
  html, body { width: 1200px; height: 876px; overflow: hidden; }
  body {
    background: var(--stage);
    font-family: "Comfortaa", sans-serif;
    position: relative;
  }
  .card {
    position: absolute;
    width: 620px;
    height: 354px;
    overflow: hidden;
    box-shadow: 0 6px 18px rgba(0,0,0,.18);
  }

  /* Front */
  .card--front { left: 60px; top: 60px; background: var(--sky); }
  .card--front .base-band {
    position: absolute; left: 0; right: 0; bottom: 0; height: 46px;
    background: var(--sand);
  }
  .brand {
    position: absolute; left: 0; right: 0; top: 34px;
    display: flex; flex-direction: column; align-items: center; gap: 18px;
  }
  .brand__dot {
    width: 132px; height: 132px; border-radius: 50%; background: var(--cocoa);
  }
  .brand__name {
    font-weight: 700; font-size: 46px; line-height: 1; color: var(--marigold);
    letter-spacing: .5px; white-space: nowrap;
  }
  .front-web {
    position: absolute; left: 0; right: 0; top: 268px; text-align: center;
    font-size: 15px; color: var(--ink);
  }

  /* Back */
  .card--back { left: 520px; top: 462px; background: var(--sand); }
  .card--back .base-band {
    position: absolute; left: 0; right: 0; bottom: 0; height: 28px;
    background: var(--sky);
  }
  .back-mark {
    position: absolute; left: 56px; top: 116px;
    width: 150px; height: 150px; background: var(--cocoa);
  }
  .cat-art {
    position: absolute; left: 372px; top: 14px; width: 210px; height: 112px;
    background: linear-gradient(180deg, #6a433c, var(--cocoa));
    border-radius: 60px 60px 0 0;
  }
  .name-band {
    position: absolute; left: 252px; top: 112px; width: 368px; height: 56px;
    background: var(--slate-teal);
    display: flex; align-items: center; padding-left: 24px;
  }
  .name-band__text {
    font-size: 31px; color: var(--marigold); font-weight: 400; white-space: nowrap;
  }
  .contacts {
    position: absolute; right: 24px; top: 188px;
    list-style: none; display: flex; flex-direction: column; gap: 10px;
  }
  .contacts__item {
    display: flex; align-items: center; justify-content: flex-end; gap: 10px;
    font-size: 14px; color: var(--ink); white-space: nowrap;
  }
  .contacts__icon { width: 16px; height: 16px; flex: none; }
</style>
</head>
<body>
  <section class="card card--front" aria-label="Business card front">
    <div class="brand">
      <span class="brand__dot"></span>
      <span class="brand__name">Purrnest Nook Co</span>
    </div>
    <div class="front-web">www.purrnestnookco.com</div>
    <div class="base-band"></div>
  </section>

  <section class="card card--back" aria-label="Business card back">
    <div class="back-mark" aria-hidden="true"></div>
    <div class="cat-art" role="img" aria-label="Cartoon cat peeking over the name band"></div>
    <div class="name-band"><span class="name-band__text">Purrnest Nook Co</span></div>
    <ul class="contacts">
      <li class="contacts__item">+1 (808) 571 6023
        <svg class="contacts__icon" viewBox="0 0 16 16"><path d="M4 1h3l1 4-2 1a9 9 0 0 0 4 4l1-2 4 1v3a2 2 0 0 1-2 2A13 13 0 0 1 2 3a2 2 0 0 1 2-2z" fill="#56342f"/></svg>
      </li>
      <li class="contacts__item">support@purrnestnookco.com
        <svg class="contacts__icon" viewBox="0 0 16 16"><rect x="1" y="3" width="14" height="10" fill="#56342f"/><path d="M1 3l7 6 7-6" fill="none" stroke="#e9dcbb" stroke-width="1.2"/></svg>
      </li>
      <li class="contacts__item">www.purrnestnookco.com
        <svg class="contacts__icon" viewBox="0 0 16 16" fill="none" stroke="#56342f" stroke-width="1.2"><circle cx="8" cy="8" r="6.5"/><ellipse cx="8" cy="8" rx="3" ry="6.5"/><path d="M1.5 8h13M2.5 4.5h11M2.5 11.5h11"/></svg>
      </li>
    </ul>
    <div class="base-band"></div>
  </section>
</body>
</html>
```